Website for Briar Hollow Gathering Church

Wordpress website design required for Briar Hollow Gathering Church. We are a family oriented church catering for age groups from school age to elderly people. The church has a wide variety of activities which it coordinates. The idea is to describe the activities on the activities page, but cross-link them to show which would be applicable to the different age groups.

We would like an inviting website which is easy to read and navigate.

Target Market(s)

Very wide audience - from school age youth to elderly people, so design and style should cater for both audiences.

Industry/Entity Type

Church

Coding

Coded - Design and coding required

Number of Pages Required

5+ page

Font styles to use
Sans Serif

Colors
0255a3
ffffff
0792cd
f78f20

Requirements
Must have
• Inviting website.
• Clear readable font.
• Space to import photos to balance text on each page.
• Need to project a dynamic and progressive feel for the church.
• Easy to navigate.
Nice to have
• Scrolling photos on pages. Ability to enter questions/ comments/prayer requests on Home page.
Should not have
• Conservative audience, so should not be too bold.

```html
<!DOCTYPE html>
<html lang="en">
<head>
<meta charset="utf-8">
<title>Briar Hollow Gathering Church</title>
<link rel="stylesheet" href="https://fonts.googleapis.com/css2?family=Open+Sans:wght@400;600;700&family=Roboto+Condensed:wght@400;700&family=Oswald:wght@500;600&display=swap">
<style>
:root{
  --navy:#0255a3;
  --blue:#0792cd;
  --band:#1f95d3;
  --orange:#f78f20;
  --white:#ffffff;
  --ink:#333333;
  --muted:#555555;
  --line:#d9d9d9;
  --footer:#151515;
  --footer-bar:#0a86c8;
}
*{box-sizing:border-box;margin:0;padding:0}
html,body{width:1200px;height:2469px;overflow:hidden}
body{font-family:"Open Sans",Arial,sans-serif;color:var(--ink);background:var(--white);position:relative}
.wrap{width:1004px;margin:0 auto;position:relative}

/* header */
.site-header{height:109px;border-top:3px solid var(--blue);position:relative;background:var(--white)}
.brand{position:absolute;left:99px;top:54px;display:flex;align-items:center;gap:10px}
.brand-dot{width:18px;height:18px;border-radius:50%;background:var(--navy)}
.brand-name{font-family:"Open Sans",sans-serif;font-weight:600;font-size:17px;color:var(--navy)}
.header-contact{position:absolute;right:99px;top:18px;display:flex;align-items:center;gap:8px;font-size:15px;color:#333}
.header-contact .phone-ico{width:28px;height:28px;margin-right:18px}
.social{width:24px;height:24px;border:1.5px solid #777;border-radius:50%}
.main-nav{position:absolute;right:99px;top:68px;display:flex;gap:0}
.main-nav a{font-family:"Roboto Condensed",sans-serif;font-size:13.5px;color:#333;text-decoration:none;text-transform:uppercase;margin-left:33px;position:relative;height:41px}
.main-nav a.active{color:var(--blue)}
.main-nav a.active::after{content:"";position:absolute;left:0;right:0;bottom:0;height:3px;background:var(--blue)}

/* hero */
.hero{height:490px;position:relative;background:linear-gradient(180deg,#6a5638 0%,#8a6f48 35%,#5a4a37 70%,#3b3129 100%);overflow:hidden}
.hero-photo{position:absolute;inset:0;background:radial-gradient(ellipse at 50% 30%,rgba(210,180,120,.55),rgba(0,0,0,0) 60%)}
.hero-title{position:absolute;left:0;right:0;top:312px;text-align:center;font-family:"Oswald",sans-serif;font-weight:600;font-size:46px;line-height:53px;color:var(--white);text-transform:uppercase;text-shadow:0 0 10px rgba(7,146,205,.9)}
.hero-dots{position:absolute;top:433px;left:0;right:0;display:flex;justify-content:center;gap:8px}
.hero-dots span{width:11px;height:11px;border-radius:50%;background:var(--white)}
.hero-dots span.on{box-shadow:0 0 0 2px rgba(255,255,255,.5);background:#ddd;border:2px solid #fff}

/* enquiry */
.enquiry{height:112px;background:var(--band)}
.enquiry form{position:relative;height:112px}
.field{position:absolute;top:22px}
.field label{display:block;font-weight:700;font-size:13.5px;color:var(--white);text-transform:uppercase;margin-bottom:11px}
.field .input{height:36px;background:var(--white);font-size:12.5px;color:#777;padding:10px 12px}
.f1{left:0;width:282px}.f2{left:300px;width:255px}.f3{left:575px;width:245px}
.send-btn{position:absolute;left:846px;top:51px;width:158px;height:36px;background:var(--orange);color:var(--white);font-weight:700;font-size:13.5px;text-transform:uppercase;display:flex;align-items:center;justify-content:center;border-radius:2px}

/* section headings */
.section-title{font-family:"Roboto Condensed",sans-serif;font-size:30px;text-transform:uppercase;text-align:center;color:#333;font-weight:400}

/* activities */
.activities{padding-top:42px}
.activity-grid{display:grid;grid-template-columns:repeat(3,326px);gap:13px;margin-top:22px}
.activity-card{border:1px solid var(--line);height:268px}
.activity-photo{height:178px;border-bottom:3px solid var(--blue)}
.ph1{background:linear-gradient(135deg,#3a2416,#7a4a28 55%,#2a1a10)}
.ph2{background:linear-gradient(160deg,#2b1a10,#9a6a35 50%,#d8b27a 75%,#3a2614)}
.ph3{background:linear-gradient(135deg,#8a8f96,#c9b7a6 50%,#6b4a40)}
.activity-card h3{font-weight:400;font-size:16px;text-align:center;margin-top:15px;color:#333}
.activity-card p{font-size:11.8px;line-height:18px;text-align:center;color:var(--muted);margin-top:5px;padding:0 20px}

/* minister's weekly */
.weekly{padding-top:38px}
.weekly-grid{display:grid;grid-template-columns:repeat(3,326px);gap:13px;margin-top:22px}
.post-card{border:1px solid #cfcfcf;height:192px;padding:16px 18px;background:#fbfbfb}
.post-card h3{font-weight:400;font-size:15.5px;text-transform:uppercase;color:#333}
.post-date{font-style:italic;font-size:12px;color:var(--orange);margin-top:8px}
.post-card p{font-size:11.8px;line-height:21px;color:var(--muted);margin-top:6px}
.read-more{font-size:13px;color:#333;margin-top:2px;display:block}
.pager{display:flex;justify-content:center;gap:10px;margin-top:26px}
.pager svg{width:14px;height:14px}

/* latest news */
.news{position:absolute;top:1449px;left:0;width:1200px;height:451px;background:linear-gradient(135deg,#1b8fce,#2aa2dc 50%,#1b8fce)}
.news .section-title{color:var(--white);margin-top:57px;font-size:32px}
.news-sub{text-align:center;color:var(--white);font-weight:600;font-size:13.5px;margin-top:3px}
.news-grid{display:grid;grid-template-columns:repeat(4,1fr);gap:6px;margin-top:37px}
.news-item{height:222px;position:relative;border:1.5px solid rgba(255,255,255,.6)}
.n1{background:linear-gradient(135deg,#e6e6e6,#c9a58a 55%,#f2f2f2)}
.n2{background:linear-gradient(135deg,#243a5a,#8a6a52 50%,#c9a040)}
.n3{background:linear-gradient(135deg,#d2b08a,#e8d8c8 45%,#3e8a4a)}
.n4{background:linear-gradient(180deg,#4a6ca8,#8aa4cf 40%,#a87a55 75%,#6a4a35)}
.news-caption{position:absolute;left:20px;top:141px;background:rgba(255,255,255,.92);padding:6px 10px;font-size:15px;color:#333}
.news-date{position:absolute;left:20px;top:181px;background:var(--orange);color:var(--white);font-size:12px;padding:3px 8px}

/* subscription */
.subscribe{position:absolute;top:1900px;left:0;width:1200px;height:241px;text-align:center}
.subscribe .section-title{margin-top:54px}
.subscribe-sub{font-size:16px;color:#444;margin-top:8px}
.sub-form{position:absolute;top:141px;left:268px;display:flex}
.sub-field{display:flex;height:43px;border:1px solid #d5d5d5}
.sub-field .ico{width:37px;background:#f0f0f0;border-right:1px solid #d5d5d5;display:flex;align-items:center;justify-content:center}
.sub-field .ico svg{width:13px;height:13px}
.sub-field .ph{font-size:13.5px;color:#777;padding:12px 14px;text-align:left}
.sf1{width:300px}.sf2{width:256px;margin-left:18px;border-right:none}
.sign-btn{width:89px;height:43px;background:var(--footer-bar);color:var(--white);font-weight:600;font-size:14px;display:flex;align-items:center;justify-content:center;text-transform:uppercase}

/* footer */
.site-footer{position:absolute;top:2141px;left:0;width:1200px;height:275px;background:linear-gradient(180deg,#1c1a18,#0e0d0c)}
.fcol{position:absolute;top:45px;color:var(--white)}
.fcol h4{font-weight:700;font-size:16px;text-transform:uppercase;margin-bottom:14px}
.fcol ul{list-style:none}
.fcol li{font-size:12.5px;line-height:24px;display:flex;align-items:center;gap:10px}
.fcol li svg{width:12px;height:12px;flex:none}
.c1{left:97px}.c2{left:367px}.c3{left:560px}.c4{left:889px}
.map{width:261px;height:153px;margin-top:0;background:linear-gradient(135deg,#d8d8d8,#bdbdbd);border:3px solid #eee}
.contact-list li{align-items:flex-start;line-height:20px;margin-bottom:14px}
.contact-list li svg{margin-top:4px;width:14px;height:14px}
.footer-bar{position:absolute;top:2416px;left:0;width:1200px;height:53px;background:var(--footer-bar);color:var(--white);font-size:12.5px;text-align:center;line-height:53px}
</style>
</head>
<body>

<header class="site-header">
  <div class="brand"><span class="brand-dot"></span><span class="brand-name">Briar Hollow Gathering Church</span></div>
  <div class="header-contact">
    <span>Toll-Free: +61.400 555 018</span>
    <svg class="phone-ico" viewBox="0 0 28 28"><circle cx="14" cy="14" r="12.5" fill="none" stroke="#0792cd" stroke-width="2"/><path d="M10 8c1 0 2 2.5 2 3s-1.2 1-1 1.8c.6 1.8 2 3.2 3.4 3.8.8.2 1.2-1 1.8-1s3 1 3 2-1.5 2.4-2.8 2.2C12.5 19.8 8.5 15.6 7.8 11 7.6 9.6 9 8 10 8z" fill="#0792cd"/></svg>
    <span class="social"></span><span class="social"></span><span class="social"></span><span class="social"></span>
  </div>
  <nav class="main-nav">
    <a class="active">Home</a><a>Age Group</a><a>Activites</a><a>Events Calendar</a><a>About BHGC</a><a>Contact Us</a>
  </nav>
</header>

<section class="hero">
  <div class="hero-photo" role="img" aria-label="Photo of a congregation seated in a tall stone church nave"></div>
  <h1 class="hero-title">Welcome to<br>Briar Hollow Gathering Church</h1>
  <div class="hero-dots"><span class="on"></span><span></span><span></span><span></span></div>
</section>

<section class="enquiry">
  <form class="wrap">
    <div class="field f1"><label>Questions *</label><div class="input">Enter questions</div></div>
    <div class="field f2"><label>Comments *</label><div class="input">Enter comments</div></div>
    <div class="field f3"><label>Prayer Requests *</label><div class="input">Enter prayer requests</div></div>
    <div class="send-btn">Send Enquiry</div>
  </form>
</section>

<section class="activities wrap">
  <h2 class="section-title">Our Activites</h2>
  <div class="activity-grid">
    <article class="activity-card"><div class="activity-photo ph1" role="img" aria-label="Photo of a person praying in a candle-lit pew"></div><h3>Sed ut perspiciatis unde omnis</h3><p>Lorem ipsum dolor sit amet, consec teer adipiscing. Prsent vestibulum molestie la my hendrerit</p></article>
    <article class="activity-card"><div class="activity-photo ph2" role="img" aria-label="Photo of an open bible in warm light"></div><h3>Sed ut perspiciatis unde omnis</h3><p>Lorem ipsum dolor sit amet, consec teer adipiscing. Prsent vestibulum molestie la my hendrerit</p></article>
    <article class="activity-card"><div class="activity-photo ph3" role="img" aria-label="Photo of a young woman praying in a busy hall"></div><h3>Sed ut perspiciatis unde omnis</h3><p>Lorem ipsum dolor sit amet, consec teer adipiscing. Prsent vestibulum molestie la my hendrerit</p></article>
  </div>
</section>

<section class="weekly wrap">
  <h2 class="section-title">Minister's Weekly</h2>
  <div class="weekly-grid">
    <article class="post-card"><h3>Sed ut perspiciatis und</h3><div class="post-date">AUG 10, 2016, 03:44 AM IST</div><p>Nulla at diam ornare, aliquam urna vel, commo urna. Nam id risus a est luctus consectetur quis eget libero. Suspendisse potenti. Pellentesque habitant morbi tristique senectus</p><span class="read-more">Read More +</span></article>
    <article class="post-card"><h3>Sed ut perspiciatis und</h3><div class="post-date">AUG 10, 2016, 03:44 AM IST</div><p>Nulla at diam ornare, aliquam urna vel, commo urna. Nam id risus a est luctus consectetur quis eget libero. Suspendisse potenti. Pellentesque habitant morbi tristique senectus</p><span class="read-more">Read More +</span></article>
    <article class="post-card"><h3>Sed ut perspiciatis und</h3><div class="post-date">AUG 10, 2016, 03:44 AM IST</div><p>Nulla at diam ornare, aliquam urna vel, commo urna. Nam id risus a est luctus consectetur quis eget libero. Suspendisse potenti. Pellentesque habitant morbi tristique senectus</p><span class="read-more">Read More +</span></article>
  </div>
  <div class="pager">
    <svg viewBox="0 0 14 14"><path d="M12 7H2M6 3L2 7l4 4" fill="none" stroke="#333" stroke-width="1.6"/></svg>
    <svg viewBox="0 0 14 14"><path d="M2 7h10M8 3l4 4-4 4" fill="none" stroke="#333" stroke-width="1.6"/></svg>
  </div>
</section>

<section class="news">
  <div class="wrap">
    <h2 class="section-title">Latest News</h2>
    <p class="news-sub">Sed ut perspiciatis unde omnis iste natus error sit voluptatem</p>
    <div class="news-grid">
      <article class="news-item n1" role="img" aria-label="Photo of two women reading together"><span class="news-caption">Sed ut perspiciatis unde</span><span class="news-date">13 AUG 2016</span></article>
      <article class="news-item n2" role="img" aria-label="Photo of a mother and baby lighting candles"><span class="news-caption">Sed ut perspiciatis unde</span><span class="news-date">13 AUG 2016</span></article>
      <article class="news-item n3" role="img" aria-label="Photo of a child at a family gathering"><span class="news-caption">Sed ut perspiciatis unde</span><span class="news-date">13 AUG 2016</span></article>
      <article class="news-item n4" role="img" aria-label="Photo of a gothic cathedral facade"><span class="news-caption">Sed ut perspiciatis unde</span><span class="news-date">13 AUG 2016</span></article>
    </div>
  </div>
</section>

<section class="subscribe">
  <h2 class="section-title">Subscription Plans</h2>
  <p class="subscribe-sub">Duis non lorem porta, eros sit amet, tempor sem. Donec nunc arcu</p>
  <div class="sub-form">
    <div class="sub-field sf1"><span class="ico"><svg viewBox="0 0 13 13"><circle cx="6.5" cy="4" r="3" fill="#999"/><path d="M1 13c0-3.5 2.5-5 5.5-5s5.5 1.5 5.5 5z" fill="#999"/></svg></span><span class="ph">Your Name</span></div>
    <div class="sub-field sf2"><span class="ico"><svg viewBox="0 0 13 13"><rect x="1" y="3" width="11" height="8" fill="none" stroke="#999" stroke-width="1.2"/><path d="M1 3l5.5 4.5L12 3" fill="none" stroke="#999" stroke-width="1.2"/></svg></span><span class="ph">Your Mail</span></div>
    <div class="sign-btn">Sign Up</div>
  </div>
</section>

<footer class="site-footer" role="img" aria-label="Dark church interior backdrop">
  <div class="fcol c1">
    <h4>Service Times</h4>
    <ul>
      <li><svg viewBox="0 0 12 12"><circle cx="6" cy="6" r="5" fill="none" stroke="#fff" stroke-width="1.5"/><path d="M6 3v3h2" fill="none" stroke="#fff" stroke-width="1.3"/></svg>Sunday @ 8:00 AM - Chapel</li>
      <li><svg viewBox="0 0 12 12"><circle cx="6" cy="6" r="5" fill="none" stroke="#fff" stroke-width="1.5"/><path d="M6 3v3h2" fill="none" stroke="#fff" stroke-width="1.3"/></svg>9:30 AM &amp; 11:00 AM - Sanctuary</li>
      <li><svg viewBox="0 0 12 12"><circle cx="6" cy="6" r="5" fill="none" stroke="#fff" stroke-width="1.5"/><path d="M6 3v3h2" fill="none" stroke="#fff" stroke-width="1.3"/></svg>Sunday @ 5:30 pm - Chapel</li>
      <li><svg viewBox="0 0 12 12"><circle cx="6" cy="6" r="5" fill="none" stroke="#fff" stroke-width="1.5"/><path d="M6 3v3h2" fill="none" stroke="#fff" stroke-width="1.3"/></svg>Sunday @ 8:00 AM - Chapel</li>
      <li><svg viewBox="0 0 12 12"><circle cx="6" cy="6" r="5" fill="none" stroke="#fff" stroke-width="1.5"/><path d="M6 3v3h2" fill="none" stroke="#fff" stroke-width="1.3"/></svg>9:30 AM &amp; 11:00 AM - Sanctuary</li>
      <li><svg viewBox="0 0 12 12"><circle cx="6" cy="6" r="5" fill="none" stroke="#fff" stroke-width="1.5"/><path d="M6 3v3h2" fill="none" stroke="#fff" stroke-width="1.3"/></svg>Sunday @ 5:30 pm - Chapel</li>
    </ul>
  </div>
  <div class="fcol c2">
    <h4>Quick Links</h4>
    <ul>
      <li><svg viewBox="0 0 12 12"><path d="M4 3l4 3-4 3z" fill="#fff"/></svg>Home</li>
      <li><svg viewBox="0 0 12 12"><path d="M4 3l4 3-4 3z" fill="#fff"/></svg>About Bhgc</li>
      <li><svg viewBox="0 0 12 12"><path d="M4 3l4 3-4 3z" fill="#fff"/></svg>Age Group</li>
      <li><svg viewBox="0 0 12 12"><path d="M4 3l4 3-4 3z" fill="#fff"/></svg>Activites</li>
      <li><svg viewBox="0 0 12 12"><path d="M4 3l4 3-4 3z" fill="#fff"/></svg>Events Calendar</li>
      <li><svg viewBox="0 0 12 12"><path d="M4 3l4 3-4 3z" fill="#fff"/></svg>Contact</li>
    </ul>
  </div>
  <div class="fcol c3">
    <h4>Our Location</h4>
    <div class="map" role="img" aria-label="Street map showing the church location"></div>
  </div>
  <div class="fcol c4">
    <h4>Contacts</h4>
    <ul class="contact-list">
      <li><svg viewBox="0 0 14 14"><path d="M7 1a4.5 4.5 0 0 0-4.5 4.5C2.5 9 7 13 7 13s4.5-4 4.5-7.5A4.5 4.5 0 0 0 7 1z" fill="#fff"/><circle cx="7" cy="5.5" r="1.7" fill="#151515"/></svg><span>Briar Hollow Gathering Church<br>PO BOX 42, 17 Larkspur Lane,<br>Fernvale, NSW 2999</span></li>
      <li><svg viewBox="0 0 14 14"><path d="M4 1c1 0 2 2.5 2 3s-1.2 1-1 1.8c.6 1.8 2 3.2 3.4 3.8.8.2 1.2-1 1.8-1s3 1 3 2-1.5 2.4-2.8 2.2C6 12.3 1.8 8 1.2 3.5 1 2.3 3 1 4 1z" fill="#fff"/></svg><span>Call Us: 1800 555 019</span></li>
      <li><svg viewBox="0 0 14 14"><path d="M1 3h12v8H1z" fill="#fff"/><path d="M1 3l6 4.5L13 3" fill="none" stroke="#151515" stroke-width="1.2"/></svg><span>hello@briarhollow.example</span></li>
    </ul>
  </div>
</footer>

<div class="footer-bar">Copyright 2016 | All Rights Reserved --Briar Hollow Gathering Church</div>

</body>
</html>
```